I would like a business card to match my truck wrap and logo. I would like the font to match my existing business card please.

Industry/Entity Type

Painter

Contact Information for Business Card

Rodrigo Fenwar 801-437-2190 Fenwarcoatings.utah@brelmox.com
SERVICES - Custom Paint & Stain, Interior & Exterior, Epoxy Coatings / Garage Floors, Cabinet Refinishing, Log Staining and Refinishing.

Requirements
Nice to have
• I would like to have the white and grey line like the bottom of my vehicle wrap, Light Grey to match my truck also.

```html
<!DOCTYPE html>
<html lang="en">
<head>
<meta charset="utf-8">
<title>Fenwar Coatings – Business Card</title>
<link href="https://fonts.googleapis.com/css2?family=Michroma&display=swap" rel="stylesheet">
<style>
  :root {
    --backdrop: #e6e6e6;
    --card-grey: #c4c4c4;
    --card-white: #f3f3f3;
    --line-white: #ececec;
    --blue: #0a62c2;
    --blue-dark: #0b3f8c;
    --blue-bright: #139fe0;
  }
  * { margin: 0; padding: 0; box-sizing: border-box; }
  html, body { width: 1200px; height: 788px; overflow: hidden; }
  body {
    background: var(--backdrop);
    font-family: "Michroma", "Arial", sans-serif;
    position: relative;
  }
  .card {
    position: absolute;
    left: 320px;
    width: 560px;
    height: 320px;
    box-shadow: 0 6px 18px rgba(0,0,0,.18);
    overflow: hidden;
  }
  .card-front { top: 58px; background: var(--card-grey); }
  .card-back { top: 410px; background: var(--card-grey); }
  .card-front svg { position: absolute; inset: 0; }

  .email {
    position: absolute; left: 18px; top: 13px;
    font-size: 10px; color: var(--blue); letter-spacing: .3px;
  }
  .owner-name {
    position: absolute; left: 38px; top: 100px;
    font-size: 34px; color: var(--blue); letter-spacing: 1px; line-height: 1;
  }
  .owner-phone {
    position: absolute; left: 92px; top: 146px;
    font-size: 22px; color: var(--blue-dark); letter-spacing: 1px; line-height: 1;
  }
  .brand {
    position: absolute; left: 392px; top: 230px;
    display: flex; align-items: center; gap: 10px;
  }
  .brand-mark { width: 30px; height: 30px; background: var(--blue); }
  .brand-name {
    font-size: 12px; color: var(--blue); line-height: 1.5; letter-spacing: .5px;
  }

  .services {
    position: absolute; left: 40px; top: 84px; color: var(--blue-bright);
  }
  .services h2 {
    font-weight: 400; font-size: 28px; letter-spacing: 1px; color: var(--blue); margin-bottom: 12px;
  }
  .services p { font-size: 13px; line-height: 1.55; }
</style>
</head>
<body>
  <section class="card card-front">
    <svg width="560" height="320" viewBox="0 0 560 320" aria-hidden="true">
      <polyline points="0,36 560,36" fill="none" stroke="var(--line-white)" stroke-width="3"/>
      <polyline points="560,204 396,204 374,226 374,284 0,284" fill="none" stroke="var(--line-white)" stroke-width="3"/>
      <polygon points="0,44 560,44 560,196 392,196 366,222 366,276 0,276" fill="var(--card-white)"/>
    </svg>
    <p class="email">Fenwarcoatings.utah@brelmox.com</p>
    <h1 class="owner-name">RODRIGO FENWAR</h1>
    <p class="owner-phone">801-437-2190</p>
    <div class="brand">
      <span class="brand-mark"></span>
      <span class="brand-name">FENWAR<br>COATINGS</span>
    </div>
  </section>

  <section class="card card-back">
    <div class="services">
      <h2>SERVICES OFFERED:</h2>
      <p>Custom Paint &amp; Stain • Interior &amp;<br>
      Exterior • Epoxy Coatings/Garage<br>
      Floors • Cabinet Refinishing • Log<br>
      Staining &amp; Refinishing</p>
    </div>
  </section>
</body>
</html>
```